We need UI/UX design for a public, informational website for The Copper Lantern.
The pages, structure, and content scope are already defined. Designers are required to work only on the UI/UX layout of these existing pages, focusing on clarity, hierarchy, spacing, and usability. Do not add, remove, rename, or reinterpret pages or content.
The website is strictly informational only. It must not include accounts, onboarding, payments, custody, escrow administration, marketplaces, dashboards, or any transactional functionality.
Scope of work
Apply UI/UX design to the predefined website pages
Design layout for text, images, notices, and sections
Ensure consistent components and layout patterns across page types
Optimize layouts for long form, compliance focused content
Content writing, page creation, and branding changes are out of scope.
Structure reference
The complete page list, hierarchy, and content definitions are provided in the technical documentation and must be treated as the primary source of truth.
A Figma link is provided only as a light visual reference for page existence and structure:
https://meadow-knot-48203956.plumsite.example/
Designers must rely on the documentation for in depth and authoritative reference.
Brand guidelines
The Copper Lantern has existing brand guidelines and official logos, including light and dark versions. These assets will be provided and must be followed exactly. Designers must not redesign, alter, or reinterpret the brand identity.
Look and feel direction
The desired visual direction is inspired by:
https://ledgerwaltz.example/
This reference is provided only to indicate:
Institutional and enterprise tone
Clean, modern typography
Strong hierarchy and generous whitespace
Editorial, content first layouts
Do not copy branding, layouts, components, or assets from the reference site.
Hero section direction
The hero section should follow a similar structural approach to the hero used on https://ledgerwaltz.example/
, meaning:
Strong editorial framing
Clear headline hierarchy
Calm, institutional first impression
However, the background video must be Abu Dhabi focused, not generic or global. The video should visually reflect:
Abu Dhabi skyline or architectural language
Institutional, sovereign, long term infrastructure tone
Clean, slow, cinematic motion
No promotional, marketing, or lifestyle visuals
The hero must remain informational, restrained, and credible. No hype. No calls to invest. No implied participation.
Constraints
One global primary CTA only: “Continue to Halvemark” (external)
All other interactions must be informational
No visuals or language implying offers, investment, eligibility, or participation
Clear separation between informational content and any external operational platforms
Deliverables
High fidelity UI/UX designs created in Figma, covering:
Desktop layouts
Tablet layouts where relevant
Mobile layouts
Complete Figma file(s) including:
All designed pages defined in the technical documentation
A reusable component library (headers, footers, cards, notice panels, forms, CTAs, typography styles, spacing system)
Clearly defined layout grids, spacing rules, and text styles
Proper use of components and variants, not detached frames
Designs prepared for developer handoff, including:
Clear layer naming and structure
Auto layout where appropriate
Consistent use of styles and components
Responsive behavior demonstrated within Figma
Notes or annotations only where necessary for clarity
No prototypes, interactions, or motion design beyond basic layout states, unless explicitly requested. The focus is static UI/UX clarity, not animation.
A detailed technical specification document and official brand assets will be provided.
Any designs delivered outside Figma, that alter structure or content, or that ignore the defined constraints, boundaries, or tone will be rejected.

```html
<!DOCTYPE html>
<html lang="en">
<head>
<meta charset="utf-8">
<title>The Copper Lantern — Governance Framework</title>
<link rel="stylesheet" href="https://fonts.googleapis.com/css2?family=Sora:wght@600;700;800&family=Plus+Jakarta+Sans:wght@400;500;600;700&display=swap">
<style>
:root{
  --purple:#6b3fb0;
  --purple-btn:#6d42b3;
  --ink:#2b2b2b;
  --body:#4a4a4a;
  --muted:#6a6a6a;
  --dark:#242424;
  --white:#ffffff;
  --rule:#d6d6d6;
}
*{margin:0;padding:0;box-sizing:border-box}
html,body{width:1200px;height:3908px;overflow:hidden;background:var(--white)}
body{position:relative;font-family:"Plus Jakarta Sans",sans-serif;color:var(--body)}
.abs{position:absolute}

/* hero */
.hero{left:0;top:0;width:1200px;height:678px;overflow:hidden;
  background:linear-gradient(180deg,#27445a 0%,#1f3546 30%,#263a43 60%,#1b2a31 100%)}
.hero-scene{position:absolute;inset:0;
  background:radial-gradient(ellipse at 80% 30%,rgba(120,160,180,.55),transparent 55%),
             radial-gradient(ellipse at 95% 85%,rgba(150,140,110,.5),transparent 45%),
             radial-gradient(ellipse at 20% 60%,rgba(60,70,75,.6),transparent 60%),
             linear-gradient(90deg,rgba(10,15,20,.55),rgba(10,15,20,.1))}
.logo{left:137px;top:44px;font-family:"Plus Jakarta Sans",sans-serif;font-weight:500;font-size:20px;letter-spacing:.5px;color:var(--white);white-space:nowrap}
.nav{top:48px;left:0;width:1200px;height:20px}
.nav a{position:absolute;top:0;font-size:14.5px;font-weight:500;color:var(--white);text-decoration:none}
.nav .active::before{content:"";position:absolute;left:0;right:0;top:-13px;height:2px;background:var(--white)}
.hero-title{left:143px;top:244px;width:520px;font-family:"Sora",sans-serif;font-weight:800;font-size:38px;line-height:48px;color:var(--white);letter-spacing:-.5px}
.hero-sub{left:143px;top:396px;width:490px;font-size:13.5px;line-height:24px;font-weight:500;color:var(--white)}
.btn{display:flex;align-items:center;justify-content:center;background:var(--purple-btn);color:var(--white);font-family:"Sora",sans-serif;font-weight:700;font-size:14px;border-radius:26px;text-decoration:none}
.hero-btn{left:141px;top:455px;width:231px;height:49px}
.hero-link{left:390px;top:470px;font-family:"Sora",sans-serif;font-weight:700;font-size:14px;color:var(--white);text-decoration:underline}
.arrow{width:46px;height:46px;border-radius:50%;background:var(--white);top:567px;display:flex;align-items:center;justify-content:center}

/* intro */
.intro-title{left:0;top:780px;width:1200px;text-align:center;font-family:"Sora",sans-serif;font-weight:800;font-size:42px;letter-spacing:-1px;color:var(--purple)}
.intro-text{left:152px;width:896px;text-align:center;font-size:14px;line-height:24px;font-weight:500;color:var(--body)}

/* timeline */
.rail{left:600px;top:1092px;width:2px;height:1836px;
  background:repeating-linear-gradient(180deg,#777 0 2px,transparent 2px 28px)}
.node{left:594px;width:14px;height:14px;border-radius:50%;background:#222}
.tile{left:144px;width:390px;border-radius:40px}
.item{left:657px;width:400px}
.item h2{font-family:"Sora",sans-serif;font-weight:600;font-size:29px;line-height:40px;color:var(--ink);letter-spacing:-.6px;margin-bottom:8px;text-transform:uppercase}
.item p{font-size:14px;line-height:24px;font-weight:500;color:var(--body);text-align:justify}
.item h3{font-family:"Sora",sans-serif;font-weight:700;font-size:20px;color:var(--purple);margin:14px 0 6px}
.item .plain{text-align:left;width:390px}
.mid-btn{left:484px;top:2966px;width:231px;height:49px}

/* contact band */
.band{left:0;top:3114px;width:1200px;height:389px;background:var(--dark)}
.band h2{position:absolute;top:105px;width:1200px;text-align:center;font-family:"Sora",sans-serif;font-weight:600;font-size:38px;letter-spacing:-.8px;color:var(--white)}
.band p{position:absolute;left:255px;top:156px;width:690px;text-align:center;font-size:14px;line-height:24px;font-weight:500;color:var(--white)}
.band-btn{left:501px;top:243px;width:198px;height:49px}

/* footer */
.foot-h{top:3596px;font-family:"Sora",sans-serif;font-weight:700;font-size:21px;color:var(--purple);letter-spacing:-.4px}
.foot-text{left:141px;top:3637px;width:410px;font-size:14px;line-height:24px;font-weight:500;color:var(--body)}
.foot-list{top:3641px;list-style:none}
.foot-list li{font-size:14px;line-height:24px;font-weight:500;color:var(--muted)}
.foot-rule{left:143px;top:3835px;width:913px;height:1px;background:var(--rule)}
.copy{left:0;top:3855px;width:1160px;text-align:center;font-size:14px;font-weight:500;color:var(--body)}
</style>
</head>
<body>

<header class="abs hero">
  <div class="hero-scene" role="img" aria-label="Aerial view of the Abu Dhabi skyline with towers, coastline and sea"></div>
  <div class="abs logo">THE COPPER LANTERN</div>
  <nav class="abs nav">
    <a class="active" style="left:432px">Home</a>
    <a style="left:507px">Framework</a>
    <a style="left:624px">Projects</a>
    <a style="left:716px">Halvemark</a>
    <a style="left:818px">Insights</a>
    <a style="left:907px">Company</a>
    <a style="left:1009px">Contact</a>
  </nav>
  <h1 class="abs hero-title">A Governance Framework for Structured Project Oversight</h1>
  <p class="abs hero-sub">Clear boundaries. Institutional discipline. Transparent structures for managing risk and accountability.</p>
  <a class="abs btn hero-btn">Continue to Halvemark</a>
  <a class="abs hero-link">Learn The Framework</a>
  <div class="abs arrow" style="left:953px"><svg width="14" height="14" viewBox="0 0 14 14"><path d="M9 2 4 7l5 5" fill="none" stroke="#111" stroke-width="1.8"/></svg></div>
  <div class="abs arrow" style="left:1010px"><svg width="14" height="14" viewBox="0 0 14 14"><path d="M5 2l5 5-5 5" fill="none" stroke="#111" stroke-width="1.8"/></svg></div>
</header>

<section>
  <h2 class="abs intro-title">THE COPPER LANTERN</h2>
  <p class="abs intro-text" style="top:845px">The Copper Lantern is a governance and project origination group. Its purpose is to define structural standards and oversight principles for complex initiatives that may involve multiple parties, staged execution, and long-term accountability. This website publishes those standards and explains how responsibilities are separated across governance, operations, and project-level execution.</p>
  <p class="abs intro-text" style="top:964px">This site is informational. It does not provide onboarding, account access, eligibility checks, custody of funds, escrow administration, or transaction execution. Where operational workflows exist, they are provided through a separate operating platform under separate terms and policies.</p>
</section>

<section>
  <div class="abs rail"></div>

  <div class="abs tile" style="top:1077px;height:282px;background:linear-gradient(120deg,#5a5a5a,#cfcfcf 45%,#888 70%,#e8e8e8)" role="img" aria-label="Row of classical stone columns in black and white"></div>
  <span class="abs node" style="top:1092px"></span>
  <div class="abs item" style="top:1080px">
    <h2>Governance and project origination</h2>
    <p>Governance in this context refers to the standards that determine how projects are structured and how oversight is described. Origination refers to the initial design and definition of an initiative, including role separation, reporting expectations, and boundary setting before execution begins. The Copper Lantern focuses on these governance-level elements rather than on operating day-to-day workflows.</p>
  </div>

  <div class="abs tile" style="top:1421px;height:330px;background:radial-gradient(circle at 55% 55%,#b9d9b2,#4e8a3c 40%,#1f4d1c 85%)" role="img" aria-label="Glass globe on green grass surrounded by sustainability icons"></div>
  <span class="abs node" style="top:1441px"></span>
  <div class="abs item" style="top:1424px">
    <h2>Clear role<br>separation</h2>
    <p>The ecosystem is designed around clear separation of responsibilities. Governance activities belong at the framework layer. Operational workflows, where available, belong on a separate operating platform designed for process execution and recordkeeping. Assets and project execution, where applicable, belong at the project level through ring-fenced structures created for specific initiatives. This separation is intended to reduce ambiguity and help stakeholders understand who is responsible for what.</p>
  </div>

  <div class="abs tile" style="top:1805px;height:402px;background:radial-gradient(circle at 60% 50%,#8fb8a8,#3f7a6c 50%,#1f4a48)" role="img" aria-label="Aerial view of a wind turbine above forest through clouds"></div>
  <span class="abs node" style="top:1821px"></span>
  <div class="abs item" style="top:1808px">
    <h2>How the ecosystem works</h2>
    <p class="plain">At a high level, the ecosystem can be understood as three layers:</p>
    <h3>Governance:</h3>
    <p class="plain">Defines standards, explains role boundaries, and publishes framework information.</p>
    <h3>Operations:</h3>
    <p class="plain">Manages workflow processes such as documentation steps and record-anchored audit</p>
    <h3>Project execution:</h3>
    <p class="plain">Occurs at the project level through dedicated structures that hold responsibilities</p>
  </div>

  <div class="abs tile" style="top:2309px;height:282px;background:linear-gradient(135deg,#eef0ec,#c9cfc6 50%,#8f8a7c)" role="img" aria-label="Old key resting on banknotes"></div>
  <span class="abs node" style="top:2328px"></span>
  <div class="abs item" style="top:2312px">
    <h2>Independent escrow &amp; milestone oversight</h2>
    <p>Some initiatives use independent escrow arrangements to coordinate staged releases linked to milestone completion. Escrow can support execution discipline by requiring defined evidence before releases occur. Escrow does not guarantee outcomes, timelines, or success, and it is not administered by this website operator. This site describes the concept for clarity and transparency.</p>
  </div>

  <div class="abs tile" style="top:2685px;height:234px;background:linear-gradient(120deg,#d8d8d8,#f2f2f2 45%,#a9a9a9 80%,#b58a55)" role="img" aria-label="Stack of documents with coloured tabs and glasses"></div>
  <span class="abs node" style="top:2698px"></span>
  <div class="abs item" style="top:2688px">
    <h2>Where operational workflows happen</h2>
    <p>Operational workflows, including any onboarding or workflow participation where permitted, occur on a separate operating platform under separate terms and policies. If you need operational access, use the Halvemark page on this site to navigate externally. This website does not host those workflows.</p>
  </div>

  <a class="abs btn mid-btn">Continue to Halvemark</a>
</section>

<section class="abs band">
  <h2>CONTACT AND INQUIRIES</h2>
  <p>If you have questions about governance framework concepts, role boundaries, or information published on this website, you can contact the team using the Contact page. Do not submit sensitive personal data through public forms.</p>
  <a class="abs btn band-btn">Contact the Team</a>
</section>

<footer>
  <h4 class="abs foot-h" style="left:141px">Informational notice</h4>
  <p class="abs foot-text">This website is provided for general informational purposes only. Nothing on this site is an offer, solicitation, or professional advice.</p>
  <h4 class="abs foot-h" style="left:655px">Links</h4>
  <ul class="abs foot-list" style="left:655px">
    <li>Framework</li><li>Projects</li><li>Halvemark</li><li>Insights</li><li>Company</li><li>Contact</li>
  </ul>
  <h4 class="abs foot-h" style="left:887px">Legal</h4>
  <ul class="abs foot-list" style="left:887px">
    <li>Legal (Index)</li><li>Terms of Use</li><li>Privacy Policy</li><li>Cookie Policy</li><li>Disclaimer &amp; Risk Notices</li><li>Acceptable Use Policy</li><li>Accessibility Statement</li>
  </ul>
  <div class="abs foot-rule"></div>
  <p class="abs copy">© &nbsp;Copyrights 2026 | All Rights Reserved</p>
</footer>

</body>
</html>
```